Property management company looking for modern card design

We at Blue Heron Partners provides property management services for its residential and commercial properties, with expertise in all categories of multifamily, industrial and office projects throughout California.

We need a business card design that is professional and modern designed business card. In our field, clients get hundreds of business cards, we would like our card to stand out.

Please avoid small print.

Target Market(s)

Professionals and high end clients

Industry/Entity Type

Financial Planning

Contact Information for Business Card

Company Name: Blue Heron Partners, Name, email, license #, phone number, website blueheronpartners.com

Font styles to use
Sans Serif

Requirements
Must have
• The card design needs to be adaptable because there is a possibly we will be expanding into different sectors other than real estate. The card design should be focused on financial planning and asset management.
Nice to have
• Modern and simple business card. Eye catching. Non-standard size/shaped cards would be great.
• blueheronpartners.com
Should not have
• Too many bright color or any pictures or shapes of real estate stuff.

```html
<!DOCTYPE html>
<html lang="en">
<head>
<meta charset="utf-8">
<title>Blue Heron Partners – Business Card</title>
<link href="https://fonts.googleapis.com/css2?family=Open+Sans:wght@400;600&display=swap" rel="stylesheet">
<style>
  :root {
    --page-bg: #e9e7e4;
    --card-top: #f7f6f4;
    --kraft: #b68c62;
    --kraft-dark: #a97f55;
    --brand-red: #d21f2b;
    --rule-grey: #6f6f6f;
    --ink: #1f1a14;
  }
  * { margin: 0; padding: 0; box-sizing: border-box; }
  html, body {
    width: 1200px; height: 900px; overflow: hidden;
    background: var(--page-bg);
    font-family: "Open Sans", Arial, sans-serif;
  }
  .card {
    position: absolute; left: 120px; top: 152px;
    width: 960px; height: 596px;
    box-shadow: 0 10px 30px rgba(0,0,0,.15);
    overflow: hidden;
  }
  .card-top {
    height: 322px; background: var(--card-top);
    position: relative;
  }
  .brand-name {
    position: absolute; left: 0; right: 0; top: 100px;
    text-align: center;
    font-size: 58px; font-weight: 400; letter-spacing: 1px;
    color: var(--brand-red); line-height: 1;
  }
  .brand-rule {
    position: absolute; top: 222px; height: 1.5px; width: 340px;
    background: var(--rule-grey);
  }
  .brand-rule.left { left: 138px; }
  .brand-rule.right { right: 138px; }
  .card-band {
    height: 274px;
    background: linear-gradient(180deg, var(--kraft) 0%, var(--kraft-dark) 100%);
    position: relative; color: var(--ink);
  }
  .person {
    position: absolute; right: 548px; top: 100px; text-align: right;
  }
  .person-name { font-size: 29px; font-weight: 600; line-height: 1.2; }
  .person-title { font-size: 23px; font-weight: 400; line-height: 1.3; }
  .contact { position: absolute; left: 452px; top: 50px; }
  .license { font-size: 25px; margin-bottom: 18px; }
  .license strong { font-weight: 600; }
  .contact-line {
    display: flex; align-items: center; gap: 18px;
    font-size: 24px; line-height: 35px;
  }
  .contact-line svg { width: 18px; height: 18px; flex: none; fill: var(--ink); }
</style>
</head>
<body>
  <div class="card">
    <div class="card-top">
      <div class="brand-name">Blue Heron Partners</div>
      <span class="brand-rule left"></span>
      <span class="brand-rule right"></span>
    </div>
    <div class="card-band">
      <div class="person">
        <div class="person-name">Daniel Hartley</div>
        <div class="person-title">Managing Director</div>
      </div>
      <div class="contact">
        <div class="license"><strong>License:</strong> BHP01245</div>
        <div class="contact-line">
          <svg viewBox="0 0 24 24" aria-hidden="true"><path d="M6.6 10.8a15 15 0 0 0 6.6 6.6l2.2-2.2a1 1 0 0 1 1-.25 11 11 0 0 0 3.6.6 1 1 0 0 1 1 1V20a1 1 0 0 1-1 1A17 17 0 0 1 3 4a1 1 0 0 1 1-1h3.5a1 1 0 0 1 1 1c0 1.25.2 2.45.6 3.6a1 1 0 0 1-.25 1z"/></svg>
          <span>044-987 654 321</span>
        </div>
        <div class="contact-line">
          <svg viewBox="0 0 24 24" aria-hidden="true"><path d="M2 5h20v14H2z M3 6l9 7 9-7" fill="none" stroke="#1f1a14" stroke-width="2"/><path d="M3 6l9 7 9-7V5H3z"/></svg>
          <span>hello@mailbox.com</span>
        </div>
        <div class="contact-line">
          <svg viewBox="0 0 24 24" aria-hidden="true"><circle cx="12" cy="12" r="10"/><path d="M2 12h20M12 2c3 3 3 17 0 20M12 2c-3 3-3 17 0 20" fill="none" stroke="#b68c62" stroke-width="1.5"/></svg>
          <span>www.blueheronpartners.com</span>
        </div>
      </div>
    </div>
  </div>
</body>
</html>
```